Fernhill Shopping Centre main sign re-design project

We would like to refresh the look of the main sign we have on the corner of a block of shops to make it more contemproary and vibrant.

A picture of the existing sign which reads Fernhill Shopping Centre can be found in attached PDF and at the following URL.

http://www.quorvelprop.co.nz/~/media/Listings/Region%20Sample/Sample%20City/Sample%20CBD/418206/Images/418206_1.ashx?bc=Gainsboro&as=1&h=550&w=980&ma=1

Fernhill Shopping Centre is also know locally as Fernhill Plaza, but the key word is Fernhill.

The existing signage has a flower/clover pattern on it which I think was just added to create a bit of interest. The building is located in a town surrounded by farm land.

I do quite like the organic feel of plant leaves or certain flowers - preferably New Zealand native plants for instance - the Kowhai flower or leaf block, pohutukawa, or kaka beak - reference images can be found with google image search

Geometric patterns could also be an option.

Once again the imagery is only to soften the sign and add some interest.

Target Market(s)

The target audience is premium shopper

Industry/Entity Type

Building

Requirements
Must have
• Must have the words: Fernhill Shopping Centre.
The big M is not essential, and I would rather the emphasis was on the word Fernhill.
Should not have
• Should not be brown. We want the sign to feel more contemporary, but not too hard. The current pale brown feels too soft in comparison with the look of the building.

```html
<!DOCTYPE html>
<html lang="en">
<head>
<meta charset="utf-8">
<title>Fernhill Shopping Centre – Main Sign</title>
<link rel="stylesheet" href="https://fonts.googleapis.com/css2?family=Didact+Gothic&family=PT+Sans+Narrow:wght@700&display=swap">
<style>
  :root {
    --sign-black: #000000;
    --leaf-green: #3f6b35;
    --leaf-deep: #2c4f27;
    --glow-teal: #6f8f86;
    --field-green: #1f9447;
    --frame-white: #ffffff;
    --type-white: #ffffff;
  }
  * { margin: 0; padding: 0; box-sizing: border-box; }
  html, body {
    width: 713px;
    height: 1200px;
    overflow: hidden;
    background: var(--sign-black);
  }
  .sign {
    position: relative;
    width: 713px;
    height: 1200px;
    overflow: hidden;
    background: var(--sign-black);
  }
  .sign-backdrop {
    position: absolute;
    inset: 0;
    width: 713px;
    height: 1200px;
  }
  .name-panel {
    position: absolute;
    left: 12px;
    top: 257px;
    width: 694px;
    height: 102px;
    border: 4px solid var(--frame-white);
    background: var(--sign-black);
    display: flex;
    align-items: center;
    justify-content: center;
    overflow: hidden;
  }
  .name-panel__word {
    font-family: "Didact Gothic", "Century Gothic", sans-serif;
    font-weight: 400;
    font-size: 112px;
    line-height: 1;
    letter-spacing: 16px;
    padding-left: 16px;
    color: var(--type-white);
    white-space: nowrap;
  }
  .descriptor-panel {
    position: absolute;
    left: 24px;
    top: 836px;
    width: 682px;
    height: 206px;
    border: 3px solid var(--frame-white);
    background: linear-gradient(90deg, rgba(0,0,0,0.55) 0%, var(--sign-black) 45%);
    text-align: right;
    padding: 22px 22px 0 0;
    font-family: "PT Sans Narrow", "Arial Narrow", sans-serif;
    font-weight: 700;
    color: var(--type-white);
    white-space: nowrap;
  }
  .descriptor-panel__line--primary {
    display: block;
    font-size: 96px;
    line-height: 1;
  }
  .descriptor-panel__line--secondary {
    display: block;
    font-size: 62px;
    line-height: 1;
    margin-top: 4px;
    padding-right: 10px;
  }
</style>
</head>
<body>
<main class="sign">
  <svg class="sign-backdrop" viewBox="0 0 713 1200" xmlns="http://www.w3.org/2000/svg">
    <defs>
      <linearGradient id="lower-field" x1="0" y1="0" x2="0" y2="1">
        <stop offset="0" stop-color="#000000" stop-opacity="0"/>
        <stop offset="0.35" stop-color="#1b2a26"/>
        <stop offset="0.7" stop-color="#1e5a3c"/>
        <stop offset="1" stop-color="#1f9447"/>
      </linearGradient>
      <radialGradient id="centre-glow" gradientUnits="userSpaceOnUse" cx="440" cy="620" r="260">
        <stop offset="0" stop-color="#6f8f86" stop-opacity="0.75"/>
        <stop offset="1" stop-color="#6f8f86" stop-opacity="0"/>
      </radialGradient>
      <linearGradient id="leaf-swath" x1="1" y1="0" x2="0" y2="1">
        <stop offset="0" stop-color="#3f6b35"/>
        <stop offset="1" stop-color="#2c4f27"/>
      </linearGradient>
    </defs>
    <rect class="lower-field" x="0" y="480" width="713" height="720" fill="url(#lower-field)"/>
    <rect class="centre-glow" x="0" y="300" width="713" height="700" fill="url(#centre-glow)"/>
    <rect class="field-band" x="0" y="1070" width="713" height="130" fill="var(--field-green)"/>
    <path role="img" aria-label="Trailing clover leaf pattern, upper right"
          d="M300 10 C420 -10 560 20 713 0 L713 255 L560 255 C600 200 640 150 620 110 C560 120 480 90 430 60 C380 40 320 45 300 10 Z"
          fill="url(#leaf-swath)" opacity="0.9"/>
    <path role="img" aria-label="Diagonal band of clover leaves sweeping down to the lower left"
          d="M713 420 L713 830 C640 830 560 850 468 900 L468 1040 C380 1080 300 1150 240 1200 L0 1200 L0 690 C120 680 260 640 380 600 C500 560 600 500 713 420 Z"
          fill="url(#leaf-swath)" opacity="0.85"/>
  </svg>

  <div class="name-panel">
    <h1 class="name-panel__word">Fernhill</h1>
  </div>

  <div class="descriptor-panel">
    <span class="descriptor-panel__line--primary">Shopping</span>
    <span class="descriptor-panel__line--secondary">Centre</span>
  </div>
</main>
</body>
</html>
```